Postcard Project

I need a postcard designed 6X9 in size printed full color
Will need in the end a high resolution print ready file with crop marks
See instructions in word doc

```html
<!DOCTYPE html>
<html lang="en">
<head>
<meta charset="utf-8">
<title>Drinkware Promotions Postcard</title>
<link rel="stylesheet" href="https://fonts.googleapis.com/css2?family=Anton&family=Arimo&family=Bebas+Neue&family=Roboto+Condensed:wght@300&display=swap">
<style>
  :root {
    --page: #ffffff;
    --backdrop: #e4e4e4;
    --promo-red: #ff0000;
    --ink: #000000;
    --paper: #ffffff;
    --label: #1a1a1a;
  }
  html, body {
    margin: 0;
    padding: 0;
    width: 1200px;
    height: 872px;
    overflow: hidden;
    background: var(--page);
  }
  .backdrop {
    position: absolute;
    left: 26px;
    top: 41px;
    width: 1157px;
    height: 797px;
    background: radial-gradient(ellipse at center, #f2f2f2 0%, var(--backdrop) 100%);
  }
  .postcard {
    position: absolute;
    left: 100px;
    top: 102px;
    width: 1000px;
    height: 669px;
    box-shadow: 0 10px 26px rgba(0,0,0,0.35);
  }
  .postcard svg { display: block; }
  .headline { font-family: "Bebas Neue", "Oswald", sans-serif; fill: var(--paper); }
  .headline .accent { fill: var(--ink); }
  .product-label { font-family: "Roboto Condensed", "Arial Narrow", sans-serif; font-weight: 300; font-size: 19px; fill: var(--label); text-anchor: middle; }
  .offer { font-family: "Anton", "Impact", sans-serif; fill: var(--paper); }
  .offer .accent { fill: var(--ink); }
  .offer-red { fill: var(--promo-red); }
  .address { font-family: "Arimo", "Arial", sans-serif; fill: var(--paper); }
</style>
</head>
<body>
<div class="backdrop"></div>
<main class="postcard">
  <svg width="1000" height="669" viewBox="0 0 1000 669" xmlns="http://www.w3.org/2000/svg">
    <defs>
      <linearGradient id="steel" x1="0" x2="1"><stop offset="0" stop-color="#b9b9b9"/><stop offset="0.5" stop-color="#f1f1f1"/><stop offset="1" stop-color="#a9a9a9"/></linearGradient>
      <linearGradient id="whiteware" x1="0" x2="1"><stop offset="0" stop-color="#dcdcdc"/><stop offset="0.5" stop-color="#ffffff"/><stop offset="1" stop-color="#d6d6d6"/></linearGradient>
      <linearGradient id="stoneware" x1="0" y1="0" x2="0" y2="1"><stop offset="0" stop-color="#f6f6f2"/><stop offset="0.6" stop-color="#eeeeea"/><stop offset="0.62" stop-color="#a89778"/><stop offset="1" stop-color="#8e7c5e"/></linearGradient>
    </defs>

    <rect class="header-band" x="0" y="0" width="1000" height="131" fill="var(--promo-red)"/>
    <text class="headline" x="30" y="51" font-size="50" textLength="937" lengthAdjust="spacingAndGlyphs">DRINKWARE - <tspan class="accent">$50 OFF</tspan> ON YOUR DRINKWARE ORDER OVER <tspan class="accent">$500</tspan></text>
    <text class="headline" x="30" y="119" font-size="77" textLength="914" lengthAdjust="spacingAndGlyphs">PROMO CODE DRINK GOOD TILL <tspan class="accent">9/30/25</tspan></text>

    <rect class="product-grid" x="0" y="131" width="1000" height="310" fill="var(--paper)"/>
    <g class="product-photos">
      <rect role="img" aria-label="Product photo: silver twisted tumbler" x="149" y="138" width="51" height="105" rx="8" fill="url(#steel)"/>
      <rect role="img" aria-label="Product photo: white camp mug with lid" x="331" y="148" width="87" height="84" rx="8" fill="url(#whiteware)"/>
      <rect role="img" aria-label="Product photo: red water bottle" x="602" y="138" width="28" height="106" rx="9" fill="#c8312e"/>
      <rect role="img" aria-label="Product photo: black ceramic mug" x="805" y="144" width="95" height="85" rx="14" fill="#222222"/>
      <rect role="img" aria-label="Product photo: white and sand two-tone mug" x="110" y="282" width="90" height="108" rx="12" fill="url(#stoneware)"/>
      <rect role="img" aria-label="Product photo: red plastic stadium cup" x="356" y="288" width="66" height="97" rx="8" fill="#d61f1f"/>
      <rect role="img" aria-label="Product photo: blue sports bottle" x="595" y="284" width="38" height="112" rx="10" fill="#1f5fc4"/>
      <rect role="img" aria-label="Product photo: white tumbler with cork base" x="830" y="284" width="46" height="105" rx="6" fill="url(#whiteware)"/>
    </g>
    <g class="product-labels">
      <text class="product-label" x="154" y="268" textLength="192" lengthAdjust="spacingAndGlyphs">4731-26SL_B_BACK Black</text>
      <text class="product-label" x="395" y="268" textLength="224" lengthAdjust="spacingAndGlyphs">4732-58WH_A_BACK Full Color</text>
      <text class="product-label" x="616" y="268" textLength="195" lengthAdjust="spacingAndGlyphs">4732-41RD_B_BACK White</text>
      <text class="product-label" x="853" y="268" textLength="218" lengthAdjust="spacingAndGlyphs">4735-19BK_B_FR_3084 White</text>
      <text class="product-label" x="154" y="422" textLength="208" lengthAdjust="spacingAndGlyphs">4735-62WH_B_FR_2917 Full</text>
      <text class="product-label" x="396" y="422" textLength="178" lengthAdjust="spacingAndGlyphs">TX-3840RD_B_FR Black</text>
      <text class="product-label" x="616" y="422" textLength="210" lengthAdjust="spacingAndGlyphs">TX-3172RBL_B__5406White</text>
      <text class="product-label" x="853" y="422" textLength="223" lengthAdjust="spacingAndGlyphs">TX-3925WH_B_FR_1368Black</text>
    </g>

    <rect class="referral-panel" x="0" y="441" width="503" height="182" fill="var(--promo-red)"/>
    <text class="offer" x="26" y="485" font-size="25">REFER a Friend <tspan class="accent" font-size="39">GIVE $100, GET $100</tspan></text>
    <text class="offer" x="26" y="519" font-size="25" textLength="468" lengthAdjust="spacingAndGlyphs">Give your friends $100 off their first purchase</text>
    <text class="offer" x="26" y="550" font-size="25" textLength="417" lengthAdjust="spacingAndGlyphs">(over $500) and receive a <tspan class="accent">$100 discount</tspan></text>
    <text class="offer" x="26" y="581" font-size="25" textLength="255" lengthAdjust="spacingAndGlyphs">on any order (over <tspan class="accent">$500</tspan>).</text>
    <text class="offer" x="26" y="612" font-size="25" textLength="187" lengthAdjust="spacingAndGlyphs">Promo Code REFER</text>

    <rect class="first-purchase-panel" x="503" y="441" width="497" height="182" fill="var(--ink)"/>
    <text class="offer offer-red" x="751" y="506" font-size="68" text-anchor="middle" textLength="218" lengthAdjust="spacingAndGlyphs">$150 off</text>
    <text class="offer" x="751" y="537" font-size="25" text-anchor="middle" textLength="387" lengthAdjust="spacingAndGlyphs">your first department purchase of $500</text>
    <text class="offer offer-red" x="750" y="576" font-size="36" text-anchor="middle" textLength="312" lengthAdjust="spacingAndGlyphs">Promo Code FIRST150</text>
    <text class="offer" x="751" y="612" font-size="25" text-anchor="middle" textLength="318" lengthAdjust="spacingAndGlyphs">Promotions cannot be combined</text>

    <rect class="footer-gap" x="0" y="623" width="1000" height="2" fill="var(--paper)"/>
    <polygon class="footer-red" points="500,625 1000,625 1000,669 518,669" fill="var(--promo-red)"/>
    <polygon class="footer-black" points="0,625 490,625 509,669 0,669" fill="var(--ink)"/>
    <path class="pin-icon" d="M24.5 633 a10.5 10.5 0 0 1 10.5 10.5 c0 7 -10.5 19.5 -10.5 19.5 s-10.5 -12.5 -10.5 -19.5 a10.5 10.5 0 0 1 10.5 -10.5 z M24.5 639.5 a4 4 0 1 0 0.01 0 z" fill="var(--paper)" fill-rule="evenodd"/>
    <text class="address" x="59" y="657" font-size="35" textLength="286" lengthAdjust="spacingAndGlyphs">Address line here</text>
    <text class="offer" x="574" y="658" font-size="29" textLength="285" lengthAdjust="spacingAndGlyphs">1st purchase &amp; referral</text>
  </svg>
</main>
</body>
</html>
```